Homemaking training schools needs a Business Card design

Designer, Hello!

No special requirements, good-looking enough.
--------------------------------------------------------------------------

Name: Marcus Dole
Chairman
Tel: 0574-71948263
Mobile: 13857420916
Email: kelvora@mailnest.example
Web: www.prt2019.example
Add: No.258, LanpingJie, BeiyuanQu, Ningbo, Zhejiang

LOGO
Ningbo PRT Homemaking Training School

Target Market(s)

pregnant women, mothers, infants, the elderly and families, including cleaning, cooking, nursing training.

Industry/Entity Type

Business

Contact Information for Business Card

Name: Marcus Dole
Chairman
Tel: 0574-71948263
Mobile: 13857420916
Email: kelvora@mailnest.example
Web: www.prt2019.example

LOGO

Font styles to use
Serif
Sans Serif
Decorative

Requirements
Nice to have
• Feels: clean, specifications, safety, comfort, warmth and happiness.

```html
<!DOCTYPE html>
<html lang="en">
<head>
<meta charset="utf-8">
<title>PingRuiTang Business Card</title>
<link rel="stylesheet" href="https://fonts.googleapis.com/css2?family=Open+Sans:wght@400;600;700&display=swap">
<style>
  :root {
    --backdrop: #e9e7e3;
    --card: #f7f6f3;
    --brand-blue: #1f7fcb;
    --brand-magenta: #e0138c;
    --ink: #4a4a4a;
    --ink-strong: #222;
    --marker: #9a9a9a;
  }
  * { margin: 0; padding: 0; box-sizing: border-box; }
  html, body {
    width: 1200px; height: 987px; overflow: hidden;
    background: var(--backdrop);
    font-family: "Open Sans", Arial, sans-serif;
  }
  .card {
    position: absolute; left: 100px; top: 193px;
    width: 1000px; height: 600px;
    background: var(--card);
    box-shadow: 0 6px 24px rgba(0,0,0,.12);
    overflow: hidden;
  }
  .brand {
    position: absolute; left: 70px; top: 158px;
    display: flex; align-items: center; gap: 16px;
  }
  .brand-marker {
    width: 22px; height: 22px;
    background: var(--marker);
    flex: none;
  }
  .brand-name {
    font-size: 52px; font-weight: 600; color: var(--ink);
    letter-spacing: -0.5px; line-height: 1;
  }
  .person {
    position: absolute; right: 60px; top: 205px; text-align: right;
  }
  .person-name {
    font-size: 34px; font-weight: 700; color: var(--brand-blue); line-height: 1.2;
  }
  .person-title {
    font-size: 22px; font-weight: 700; color: var(--brand-magenta); line-height: 1.3;
  }
  .edge-mark {
    position: absolute; right: 0; top: 222px;
    width: 14px; height: 66px; background: var(--brand-blue);
  }
  .contacts {
    position: absolute; left: 55px; top: 392px; list-style: none;
  }
  .contacts li {
    display: flex; align-items: center; gap: 12px;
    font-size: 22px; color: var(--ink-strong); height: 38px;
  }
  .contacts svg { width: 22px; height: 22px; fill: var(--brand-blue); flex: none; }
  .address {
    position: absolute; right: 60px; top: 430px; text-align: right;
    font-style: normal;
    font-size: 21px; font-weight: 600; color: var(--ink-strong); line-height: 1.35;
  }
  .band-blue {
    position: absolute; left: 0; top: 548px; width: 650px; height: 16px;
    background: var(--brand-blue);
  }
  .band-magenta {
    position: absolute; left: 650px; top: 548px; right: 0; height: 24px;
    background: var(--brand-magenta);
  }
</style>
</head>
<body>
  <main class="card">
    <div class="brand">
      <span class="brand-marker"></span>
      <span class="brand-name">PingRuiTang</span>
    </div>

    <div class="person">
      <p class="person-name">Marcus Dole</p>
      <p class="person-title">Chairman</p>
    </div>
    <div class="edge-mark"></div>

    <ul class="contacts">
      <li>
        <svg viewBox="0 0 24 24" aria-hidden="true"><path d="M6.6 10.8a15.1 15.1 0 0 0 6.6 6.6l2.2-2.2c.3-.3.7-.4 1-.2 1.1.4 2.3.6 3.6.6.6 0 1 .4 1 1V20c0 .6-.4 1-1 1A17 17 0 0 1 3 4c0-.6.4-1 1-1h3.5c.6 0 1 .4 1 1 0 1.3.2 2.5.6 3.6.1.3 0 .7-.2 1z"/></svg>
        <span>0574-71948263</span>
      </li>
      <li>
        <svg viewBox="0 0 24 24" aria-hidden="true"><path d="M7 2h10a2 2 0 0 1 2 2v16a2 2 0 0 1-2 2H7a2 2 0 0 1-2-2V4a2 2 0 0 1 2-2zm0 3v13h10V5zm5 14.2a1 1 0 1 0 0 2 1 1 0 0 0 0-2z"/></svg>
        <span>13857420916</span>
      </li>
      <li>
        <svg viewBox="0 0 24 24" aria-hidden="true"><path d="M3 5h18a1 1 0 0 1 1 1v12a1 1 0 0 1-1 1H3a1 1 0 0 1-1-1V6a1 1 0 0 1 1-1zm1 2.2V17h16V7.2l-8 5.3z M5 7l7 4.6L19 7z"/></svg>
        <span>kelvora@mailnest.example</span>
      </li>
    </ul>

    <address class="address">
      No.258, LanpingJie<br>
      BeiyuanQu, Ningbo, Zhejiang<br>
      www.prt2019.example
    </address>

    <div class="band-blue"></div>
    <div class="band-magenta"></div>
  </main>
</body>
</html>
```